Professional Package for CPA Firm

We would like a stationery design for our new CPA Firm based in Atlanta, GA called 'Vale 8'. We work with investors to help grow investments, tax free. We would like the design to have a professional/minimal look with a 'wow' factor. We need 9.5″ x 4.125″, 9x12, and 10x13 mailing envelopes, business cards, and a letterhead. We have a logo that is already complete. For the letterhead, we would like to have space to put credentials at the bottom of the page

Industry/Entity Type

CPA, Accounting

```html
<!DOCTYPE html>
<html lang="en">
<head>
<meta charset="utf-8">
<title>Vale 8 Stationery Package</title>
<link href="https://fonts.googleapis.com/css2?family=Lato:wght@300;400;700&family=Great+Vibes&display=swap" rel="stylesheet">
<style>
  :root {
    --stage: #959595;
    --ink: #000000;
    --paper: #ffffff;
    --brand-blue: #0a9ad6;
    --tint-blue: #e3f2fa;
    --body-grey: #555555;
    --label: #111111;
  }
  * { box-sizing: border-box; margin: 0; padding: 0; }
  html, body { width: 1200px; height: 680px; overflow: hidden; background: var(--stage); }
  body { position: relative; font-family: 'Lato', sans-serif; color: var(--ink); }
  .piece { position: absolute; overflow: hidden; }
  .label { position: absolute; font-size: 9.5px; letter-spacing: .2px; color: var(--label); transform: translateX(-50%); white-space: nowrap; }
  .wordmark { position: absolute; font-family: 'Lato', sans-serif; font-weight: 700; color: var(--paper); letter-spacing: .5px; white-space: nowrap; }
  .tagline { position: absolute; font-family: 'Great Vibes', cursive; white-space: nowrap; }
  .icon { width: 7px; height: 7px; vertical-align: -1px; margin-right: 4px; fill: var(--brand-blue); }
  .rule-v { position: absolute; width: 1px; background: #555; }

  /* Letterhead */
  .letterhead { left: 66px; top: 47px; width: 390px; height: 553px; background: var(--paper); }
  .letterhead__header { position: absolute; left: 0; top: 0; width: 100%; height: 75px; background: var(--ink); }
  .letterhead__address { position: absolute; right: 108px; top: 27px; font-size: 6.8px; line-height: 9px; color: var(--paper); text-align: right; }
  .letterhead__address .web { color: var(--brand-blue); }
  .letterhead__contacts { position: absolute; left: 299px; top: 27px; font-size: 6.8px; line-height: 9px; color: var(--paper); }
  .letterhead__salutation { position: absolute; left: 35px; top: 155px; font-size: 10px; font-weight: 300; color: #333; }
  .letterhead__body { position: absolute; left: 35px; top: 184px; width: 324px; font-size: 5.6px; line-height: 8.4px; font-weight: 300; color: var(--body-grey); }
  .letterhead__body p { margin-bottom: 8.4px; }
  .letterhead__closing { position: absolute; left: 35px; top: 362px; font-size: 5.8px; color: var(--body-grey); }
  .letterhead__signature { position: absolute; left: 33px; top: 383px; width: 72px; height: 28px; background: var(--tint-blue); border-radius: 3px; }
  .letterhead .tagline { left: 0; width: 100%; text-align: center; top: 512px; font-size: 15px; color: #333; }

  /* Envelope */
  .envelope-back { left: 490px; top: 47px; width: 354px; height: 160px; background: var(--paper); }
  .envelope-back svg { position: absolute; left: 0; top: 0; }
  .envelope-back .wordmark { left: 0; width: 100%; text-align: center; top: 14px; font-size: 11px; }
  .envelope-back .tagline { left: 0; width: 100%; text-align: center; top: 33px; font-size: 9.5px; color: var(--paper); }
  .envelope-front { left: 544px; top: 130px; width: 355px; height: 163px; background: var(--paper); box-shadow: 0 0 3px rgba(0,0,0,.25); }
  .envelope-front__band { position: absolute; left: 0; top: 0; width: 100%; height: 62px; background: var(--ink); }
  .envelope-front .wordmark { left: 18px; top: 34px; font-size: 12px; }
  .envelope-front__address { position: absolute; left: 19px; top: 70px; font-size: 7.2px; line-height: 9px; color: #444; }

  /* Business cards */
  .card-front { left: 944px; top: 48px; width: 187px; height: 107px; background: var(--paper); }
  .card-front__id { position: absolute; right: 92px; top: 41px; text-align: right; font-size: 4px; line-height: 5px; color: #555; }
  .card-front__id .name { font-size: 6px; line-height: 7px; font-weight: 700; color: var(--brand-blue); }
  .card-front .rule-v { left: 99px; top: 41px; height: 26px; background: #888; }
  .card-front__contacts { position: absolute; left: 105px; top: 42px; font-size: 4px; line-height: 5.2px; color: #555; }
  .card-front__contacts .icon { width: 3.5px; height: 3.5px; margin-right: 2px; }
  .card-back { left: 944px; top: 182px; width: 193px; height: 110px; background: var(--ink); }
  .card-back .wordmark { left: 0; width: 100%; text-align: center; top: 51px; font-size: 15px; }
  .card-back .tagline { left: 0; width: 100%; text-align: center; top: 83px; font-size: 9px; color: var(--paper); }

  /* Email signatures */
  .sig { background: var(--ink); color: var(--paper); }
  .sig .name { color: var(--brand-blue); font-weight: 400; }
  .sig-tall { left: 490px; top: 334px; width: 175px; height: 266px; }
  .sig-tall .wordmark { left: 28px; top: 62px; font-size: 20px; }
  .sig-tall__id { position: absolute; left: 27px; top: 108px; }
  .sig-tall__id .name { font-size: 15px; line-height: 17px; }
  .sig-tall__id .role { font-size: 9.5px; }
  .sig-tall .short-rule { position: absolute; left: 28px; width: 14px; height: 1px; background: var(--brand-blue); }
  .sig-tall__address { position: absolute; left: 28px; top: 154px; font-size: 9.5px; line-height: 11.5px; }
  .sig-tall__contacts { position: absolute; left: 28px; top: 193px; font-size: 9.5px; line-height: 11.5px; }
  .sig-wide { left: 695px; top: 334px; width: 455px; height: 141px; }
  .sig-wide .wordmark { left: 37px; top: 58px; font-size: 20px; }
  .sig-wide .rule-v { left: 139px; top: 48px; height: 50px; }
  .sig-wide__id { position: absolute; left: 162px; top: 44px; font-size: 9.5px; line-height: 11.5px; }
  .sig-wide__id .name { font-size: 15.5px; line-height: 18px; }
  .sig-wide .rule-v.second { left: 297px; }
  .sig-wide__contacts { position: absolute; left: 318px; top: 49px; font-size: 9.5px; line-height: 11.5px; }
  .sig-slim { left: 695px; top: 513px; width: 455px; height: 87px; }
  .sig-slim .wordmark { left: 19px; top: 34px; font-size: 18px; }
  .sig-slim .rule-v { top: 29px; height: 32px; }
  .sig-slim__id { position: absolute; left: 101px; width: 113px; top: 32px; text-align: center; font-size: 9.5px; line-height: 11px; }
  .sig-slim__id .name { font-size: 14px; line-height: 16px; }
  .sig-slim__address { position: absolute; left: 227px; top: 28px; font-size: 9px; line-height: 11.5px; }
  .sig-slim__contacts { position: absolute; left: 350px; top: 28px; font-size: 9px; line-height: 11.5px; }
</style>
</head>
<body>
<svg width="0" height="0" style="position:absolute" aria-hidden="true">
  <defs>
    <symbol id="i-phone" viewBox="0 0 10 10"><path d="M2 0.5 L4 2.8 L3 4 Q4.5 6.3 6 7 L7.2 6 L9.5 8 L8 9.6 Q3.5 9 0.5 2 Z"/></symbol>
    <symbol id="i-mobile" viewBox="0 0 10 10"><path d="M2.5 0 H7.5 V10 H2.5 Z M3.5 1.2 V8 H6.5 V1.2 Z"/></symbol>
    <symbol id="i-mail" viewBox="0 0 10 10"><path d="M0 2 H10 V8.5 H0 Z M0.8 2.6 L5 5.8 L9.2 2.6 Z"/></symbol>
    <symbol id="i-web" viewBox="0 0 10 10"><path d="M5 0 A5 5 0 1 0 5 10 A5 5 0 1 0 5 0 Z M5 1.3 A3.7 3.7 0 1 1 5 8.7 A3.7 3.7 0 1 1 5 1.3 Z M4.3 1.5 H5.7 V8.5 H4.3 Z"/></symbol>
  </defs>
</svg>

<!-- Letterhead -->
<section class="piece letterhead">
  <header class="letterhead__header">
    <div class="wordmark" style="left:35px;top:27px;font-size:15px;">VALE 8</div>
    <div class="letterhead__address">4120 Linden Court<br>Atlanta, Georgia 30309<br><span class="web">www.vale8.com</span></div>
    <div class="rule-v" style="left:291px;top:28px;height:26px;"></div>
    <div class="letterhead__contacts">
      <div><svg class="icon"><use href="#i-phone"/></svg>404-555-0182</div>
      <div><svg class="icon"><use href="#i-mobile"/></svg>404-555-0147</div>
      <div><svg class="icon"><use href="#i-mail"/></svg>info@vale8.com</div>
    </div>
  </header>
  <p class="letterhead__salutation">Dear Mr. Hart,</p>
  <div class="letterhead__body">
    <p>Lorem ipsum dolor sit amet, consectetur adipiscing elit. Donec orci purus, luctus vitae dignissim eu, iaculis sed purus. Vivamus faucibus, ipsum nec aliquet viverra, leo mauris condimentum ligula, sit amet sagittis enim ligula quis arcu. Nam egestas tortor id nisi porttitor mattis. In tortor ante, ultricies in suscipit a, tempus non massa. Vivamus et auctor mi. Fusce vel massa nulla. Phasellus nec eros mauris, et scelerisque orci.</p>
    <p>Donec malesuada orci vitae nulla accumsan porta a id massa. Quisque accumsan iaculis magna sit amet fringilla. Maecenas consequat, magna eget tincidunt semper, odio nibh rutrum mi, id feugiat ante nisi eu risus. Vestibulum nunc orci, rhoncus a placerat in, ultricies in mi. Cras mattis varius eros, vel fringilla nisi suscipit eget. Quisque scelerisque sagittis nulla at porttitor.</p>
    <p>Sed id augue vitae urna euismod commodo aliquet a quam. Pellentesque arcu velit, cursus et malesuada ut, consequat et diam. Nullam erat sem, rhoncus id ullamcorper vitae, rhoncus et arcu. In ultricies ultricies nulla, ut rutrum nisi iaculis at. Donec eu magna a metus ornare faucibus. Fusce aliquet faucibus ultricies. Morbi semper, est id tincidunt gravida, sem arcu adipiscing lacus, ac bibendum nulla leo eu purus. Quisque nec diam sed risus consectetur accumsan quis quis nibh. Vestibulum id purus lorem.</p>
    <p>It is a long established fact that a reader will be distracted by the readable content of a page when looking at its layout. The point of using Lorem Ipsum is that it has a more-or-less normal distribution of letters, as opposed to using 'Content here, content here', making it look like readable English. Many desktop publishing packages</p>
  </div>
  <p class="letterhead__closing">Sincerely,</p>
  <div class="letterhead__signature" role="img" aria-label="Handwritten signature of Daniel Hart"></div>
  <p class="tagline">Keep More Of What You Build</p>
</section>
<div class="label" style="left:268px;top:620px;">LETTERHEAD</div>

<!-- Envelope -->
<section class="piece envelope-back">
  <svg width="354" height="160" viewBox="0 0 354 160" aria-hidden="true">
    <path d="M0 0 H354 L345 36 Q340 59 318 59 H36 Q14 59 9 36 Z" fill="var(--brand-blue)"/>
  </svg>
  <div class="wordmark">VALE 8</div>
  <p class="tagline">Keep More Of What You Build</p>
</section>
<section class="piece envelope-front">
  <div class="envelope-front__band"></div>
  <div class="wordmark">VALE 8</div>
  <p class="envelope-front__address">4120 Linden Court<br>Atlanta, Georgia 30309</p>
</section>
<div class="label" style="left:723px;top:304px;">ENVELOPE</div>

<!-- Business cards -->
<section class="piece card-front">
  <div class="card-front__id">
    <div class="name">DANIEL HART</div>
    President<br>4120 Linden Court<br>Atlanta, Georgia 30309
  </div>
  <div class="rule-v"></div>
  <div class="card-front__contacts">
    <div><svg class="icon"><use href="#i-phone"/></svg>404-555-0182</div>
    <div><svg class="icon"><use href="#i-mobile"/></svg>404-555-0163</div>
    <div><svg class="icon"><use href="#i-mail"/></svg>info@vale8.com</div>
    <div><svg class="icon"><use href="#i-web"/></svg>www.vale8.com</div>
  </div>
</section>
<div class="label" style="left:1039px;top:164px;">FRONT CARD</div>
<section class="piece card-back">
  <div class="wordmark">VALE 8</div>
  <p class="tagline">Keep More Of What You Build</p>
</section>
<div class="label" style="left:1039px;top:304px;">BACK CARD</div>

<!-- Email signature 1 -->
<section class="piece sig sig-tall">
  <div class="wordmark">VALE 8</div>
  <div class="sig-tall__id">
    <div class="name">Daniel Hart</div>
    <div class="role">President</div>
  </div>
  <div class="short-rule" style="top:145px;"></div>
  <p class="sig-tall__address">4120 Linden Court<br>Atlanta, Georgia 30309</p>
  <div class="short-rule" style="top:184px;"></div>
  <div class="sig-tall__contacts">
    <div><svg class="icon"><use href="#i-phone"/></svg>404-555-0182</div>
    <div><svg class="icon"><use href="#i-mobile"/></svg>404-555-0147</div>
    <div><svg class="icon"><use href="#i-mail"/></svg>info@vale8.com</div>
    <div><svg class="icon"><use href="#i-web"/></svg>www.vale8.com</div>
  </div>
</section>
<div class="label" style="left:581px;top:620px;">EMAIL SIGNATURE 1</div>

<!-- Email signature 2 -->
<section class="piece sig sig-wide">
  <div class="wordmark">VALE 8</div>
  <div class="rule-v"></div>
  <div class="sig-wide__id">
    <div class="name">Daniel Hart</div>
    President<br>4120 Linden Court<br>Atlanta, Georgia 30309
  </div>
  <div class="rule-v second"></div>
  <div class="sig-wide__contacts">
    <div><svg class="icon"><use href="#i-phone"/></svg>404-555-0182</div>
    <div><svg class="icon"><use href="#i-mobile"/></svg>404-555-0147</div>
    <div><svg class="icon"><use href="#i-mail"/></svg>info@vale8.com</div>
    <div><svg class="icon"><use href="#i-web"/></svg>www.vale8.com</div>
  </div>
</section>
<div class="label" style="left:909px;top:487px;">EMAIL SIGNATURE 2</div>

<!-- Email signature 3 -->
<section class="piece sig sig-slim">
  <div class="wordmark">VALE 8</div>
  <div class="rule-v" style="left:101px;"></div>
  <div class="sig-slim__id">
    <div class="name">Daniel Hart</div>
    President
  </div>
  <div class="rule-v" style="left:213px;"></div>
  <p class="sig-slim__address">4120 Linden Court<br>Atlanta, Georgia 30309<br>www.vale8.com</p>
  <div class="rule-v" style="left:334px;"></div>
  <div class="sig-slim__contacts">
    <div><svg class="icon"><use href="#i-phone"/></svg>404-555-0182</div>
    <div><svg class="icon"><use href="#i-mobile"/></svg>404-555-0147</div>
    <div><svg class="icon"><use href="#i-mail"/></svg>info@vale8.com</div>
  </div>
</section>
<div class="label" style="left:909px;top:620px;">EMAIL SIGNATURE 3</div>
</body>
</html>
```